Detail Shop Business card design

i need a business card design for my new detailing company called 'Brisk's Polish Works'. i want an all black and white design . simple, direct and to the point. i want the designer to choose a fitting font to match the logothe front should have logo, address, phone and email and the back side should have a slogan and text indicating that we offer services on anything including cars, trucks, motorcycles and RVs. slogan will read "we take pride in your ride"
maybe also very small on the back side the IG icon with Brisks_Polish_Works

phone 208.417.6352
address 3847 E Larkin Ave
Spokane WA 99214
email: BrisksPolish@mailvexo.com

Target Market(s)

all ages , auto enthusiasts

Industry/Entity Type

Automotive

Contact Information for Business Card

the front should have logo, address, phone and email and the back side should have a slogan and text indicating that we offer services on anything including cars, trucks, motorcycles and RVs. slogan will read "we take pride in your ride"

phone 208.417.6352
address 3847 E Larkin Ave
Spokane WA 99214

Colors
000000
ffffff

Requirements
Must have
• bold font and very simple design with good spacing
Nice to have
• anything creative from the designer indicating we service any types of vehicles
Should not have
• any colors ,

```html
<!DOCTYPE html>
<html lang="en">
<head>
<meta charset="utf-8">
<title>Brisk's Polish Works — Business Card</title>
<link href="https://fonts.googleapis.com/css2?family=Roboto:wght@400;500;700;900&family=Oswald:wght@400;500&display=swap" rel="stylesheet">
<style>
  :root {
    --ink: #000000;
    --paper: #ffffff;
    --card-stock: #f7f7f7;
    --muted: #555555;
    --band-grey: #6b6b6b;
    --backdrop: #e4e4e4;
  }
  * { box-sizing: border-box; margin: 0; padding: 0; }
  html, body {
    width: 1200px; height: 960px; overflow: hidden;
    background: var(--backdrop);
    font-family: "Roboto", Arial, sans-serif;
    color: var(--ink);
  }
  .canvas { position: relative; width: 1200px; height: 960px; }
  .card {
    position: absolute; width: 600px; height: 342px;
    background: var(--card-stock);
    box-shadow: 0 2px 6px rgba(0,0,0,0.25);
    overflow: hidden;
  }
  .card-front { left: 314px; top: 113px; }
  .card-back { left: 311px; top: 473px; }

  /* front */
  .brand-mark {
    position: absolute; right: 38px; top: 40px; width: 165px;
    display: flex; flex-direction: column; align-items: center; gap: 8px;
  }
  .brand-dot { width: 56px; height: 56px; border-radius: 50%; background: var(--ink); }
  .brand-name {
    font-weight: 900; font-size: 17px; text-align: center; line-height: 1.15;
    text-transform: uppercase; color: var(--ink);
  }
  .person { position: absolute; left: 35px; top: 163px; }
  .person-name { font-weight: 700; font-size: 21px; letter-spacing: 0.2px; }
  .person-title { font-size: 15px; color: var(--muted); margin-top: 3px; }
  .divider { position: absolute; left: 35px; right: 36px; top: 217px; height: 2px; background: var(--ink); }
  .contact-list { position: absolute; left: 35px; top: 231px; list-style: none; }
  .contact-list li {
    display: flex; align-items: center; gap: 8px;
    height: 19px; font-size: 14px; color: #333;
  }
  .contact-list svg { width: 12px; height: 12px; flex: none; fill: var(--ink); }
  .address {
    position: absolute; right: 36px; top: 269px; text-align: right;
    font-size: 14px; line-height: 19px; color: #333;
  }
  .band { position: absolute; bottom: 0; height: 10px; }
  .band-black { left: 0; width: 392px; background: var(--ink); }
  .band-grey { left: 394px; right: 0; background: var(--band-grey); }

  /* back */
  .back-mark {
    position: absolute; left: 50%; top: 60px; transform: translateX(-50%);
    display: flex; flex-direction: column; align-items: center; gap: 14px;
  }
  .back-mark .brand-dot { width: 110px; height: 110px; }
  .back-mark .brand-name { font-size: 30px; white-space: nowrap; }
  .slogan {
    position: absolute; left: 0; right: 0; top: 269px; text-align: center;
    font-weight: 700; font-size: 17px; letter-spacing: 0.3px; text-transform: uppercase;
  }
  .slogan-rule { position: absolute; left: 165px; width: 297px; top: 293px; height: 2px; background: var(--ink); }
  .services {
    position: absolute; left: 0; right: 0; top: 297px; text-align: center;
    font-family: "Oswald", "Arial Narrow", sans-serif; font-size: 14px; font-weight: 500;
  }
</style>
</head>
<body>
<main class="canvas">
  <section class="card card-front" aria-label="Card front">
    <div class="brand-mark">
      <span class="brand-dot"></span>
      <span class="brand-name">Brisk's Polish Works</span>
    </div>
    <div class="person">
      <p class="person-name">DALE MERROW</p>
      <p class="person-title">CEO/FOUNDER</p>
    </div>
    <div class="divider"></div>
    <ul class="contact-list">
      <li><svg viewBox="0 0 24 24"><path d="M6.6 10.8a15.1 15.1 0 0 0 6.6 6.6l2.2-2.2c.3-.3.7-.4 1-.2 1.1.4 2.3.6 3.6.6.6 0 1 .4 1 1V20c0 .6-.4 1-1 1A17 17 0 0 1 3 4c0-.6.4-1 1-1h3.5c.6 0 1 .4 1 1 0 1.3.2 2.5.6 3.6.1.3 0 .7-.2 1z"/></svg>208.417.6352</li>
      <li><svg viewBox="0 0 24 24"><path d="M7 1h10a2 2 0 0 1 2 2v18a2 2 0 0 1-2 2H7a2 2 0 0 1-2-2V3a2 2 0 0 1 2-2zm0 3v14h10V4z"/></svg>724 315 8806</li>
      <li><svg viewBox="0 0 24 24"><path d="M2 5h20v14H2zm2 2v.5l8 5 8-5V7l-8 5z"/></svg>BrisksPolish@mailvexo.com</li>
      <li><svg viewBox="0 0 24 24"><circle cx="12" cy="12" r="10"/><path d="M2 12h20M12 2c3 3 3 17 0 20M12 2c-3 3-3 17 0 20" stroke="#f7f7f7" stroke-width="1.5" fill="none"/></svg>www.briskspolish.com</li>
    </ul>
    <p class="address">3847 E Larkin Ave<br>Spokane WA 99214</p>
    <div class="band band-black"></div>
    <div class="band band-grey"></div>
  </section>

  <section class="card card-back" aria-label="Card back">
    <div class="back-mark">
      <span class="brand-dot"></span>
      <span class="brand-name">Brisk's Polish Works</span>
    </div>
    <p class="slogan">We take pride in your ride</p>
    <div class="slogan-rule"></div>
    <p class="services">we offer services on anything including cars, trucks, motorcycles &amp; RVs</p>
  </section>
</main>
</body>
</html>
```